I want a website to be designed for our new company, it's an import and export company for variety of things.

please see the attached Logo for our company and the Images for our different sections for our busienss

Target Market(s)

multiple

Coding

Coded - Design and coding required

Number of Pages Required

5+ page

Font styles to use
Sans Serif

Colors

Designer to choose colors to be used in the design.

Requirements
Must have
• KVR GLOBALINKS
• KVR globalinks Trading & Contracting provides various services. The Company offers infrastructure construction, oil, enegy and gas services, agricultural projects, real estate development, travel and tourism, and food processing and trading.
• Civil contracting for infrastructure, residential and heavy projects. Through its main subsidiaries; distribution of general food products, construction chemicals including corrosion inhibitors and electrical machinery; provides catering and travel agency services; ownership and operation of a school; offers human sources services including manpower supply.
• Drilling and Gold Mines Used Machinery, All Kinds of Construction Machinery, Drilling Machines are manufactured and sold.
Nice to have
• good designa and beautiful colours, it has too look professional

```html
<!DOCTYPE html>
<html lang="en">
<head>
<meta charset="utf-8">
<title>KVR GLOBALINKS</title>
<link href="https://fonts.googleapis.com/css2?family=Lato:wght@400;700;900&display=swap" rel="stylesheet">
<style>
:root{
  --gold:#b8862e;
  --green:#3d5e2a;
  --green-band:#4d6c37;
  --ink:#1f1f1f;
  --text:#555;
  --black:#0d0d0d;
  --nav:#1b1b1b;
  --light:#efefef;
  --footer:#1e1e1e;
  --copy:#343434;
  --navy:#1d3557;
}
*{margin:0;padding:0;box-sizing:border-box}
html,body{width:1200px;height:4011px;overflow:hidden}
body{font-family:'Lato',Arial,sans-serif;color:var(--text);background:#fff;position:relative}
.abs{position:absolute}
.topbar{left:0;top:0;width:1200px;height:51px;background:var(--black)}
.topbar .phone{left:75px;top:14px;color:#fff;font-size:17px;display:flex;align-items:center;gap:12px}
.social{display:flex;gap:14px}
.social span{width:22px;height:22px;border-radius:50%;background:#fff;display:block}
.topbar .social{right:72px;top:14px}
.navbar{left:0;top:51px;width:1200px;height:95px;background:var(--nav)}
.nav-link{top:42px;font-size:14px;font-weight:700;color:#fff;letter-spacing:.2px}
.nav-link.active{color:var(--gold)}
.brand-plate{left:0;top:0;width:1200px;height:146px}
.brand{display:flex;flex-direction:column;align-items:center;gap:8px;color:#fff;font-weight:700;font-size:17px;letter-spacing:2px}
.brand i{width:38px;height:38px;border:2px solid #fff;border-radius:50%;display:block}
.nav-brand{left:475px;top:30px;width:252px}
.hero{left:0;top:146px;width:1200px;height:575px;background:linear-gradient(180deg,#3f7ec4 0%,#8fb3d6 35%,#9c8770 62%,#4c4238 100%)}
.hero h1{left:0;top:232px;width:1200px;text-align:center;color:#fff;font-weight:900;font-size:50px;line-height:52px;letter-spacing:-.5px}
.dots{left:562px;top:674px;display:flex;gap:13px}
.dots span{width:14px;height:14px;border-radius:50%;background:#fff}
.dots span:first-child{background:var(--gold)}
.section-title{left:0;width:1200px;text-align:center;font-size:30px;font-weight:900;color:var(--ink)}
.section-title em{font-style:normal;color:var(--gold)}
.btn{display:flex;align-items:center;justify-content:center;background:var(--green);color:#fff;font-weight:900;font-size:16px;letter-spacing:.3px}
.welcome h2{left:75px;top:784px;font-size:28px;font-weight:900;color:var(--ink);line-height:34px}
.welcome h2 em{font-style:normal;color:var(--gold);display:block}
.welcome p{left:75px;width:600px;font-size:14px;line-height:26.5px}
.welcome-frame{left:705px;top:788px;width:422px;height:310px;background:var(--navy)}
.welcome-img{left:696px;top:796px;width:422px;height:309px;background:linear-gradient(135deg,#6c7787,#232a33 60%,#151a20)}
.services-band{left:0;top:1178px;width:1200px;height:746px;background:radial-gradient(ellipse at center,#fafafa 0%,var(--light) 70%)}
.svc h3{font-size:17px;font-weight:900;color:var(--green);margin-bottom:4px}
.svc p{font-size:14px;line-height:23px}
.svc.left{text-align:right}
.blog-band{left:0;top:2519px;width:1200px;height:501px;background:var(--light)}
.project h3{font-size:18px;font-weight:900;color:var(--green);text-align:center}
.project p{font-size:14px;line-height:23px;text-align:center;margin-top:8px}
.post .date{font-size:13px;font-weight:700;color:var(--gold)}
.post h4{font-size:19px;font-weight:900;color:var(--green);margin:4px 0 3px}
.post p{font-size:14px;line-height:26px;width:318px}
.quote-text{left:150px;top:3205px;width:900px;text-align:center;font-size:15px;line-height:26.5px;color:#444}
.reviewer{width:160px;text-align:center}
.reviewer .face{width:100px;height:100px;border-radius:50%;margin:0 auto 12px;background:linear-gradient(180deg,#c9c9c9,#6a6a6a);border:3px solid #fff;box-shadow:0 0 0 1px #ccc}
.reviewer .face.mid{border-color:var(--gold);box-shadow:none}
.reviewer b{display:block;font-size:14px;font-weight:900;color:var(--ink)}
.reviewer small{font-size:14px;color:#777}
.newsletter{left:0;top:3529px;width:1200px;height:88px;background:var(--green-band)}
.newsletter h5{left:75px;top:30px;font-size:21px;font-weight:900;color:#fff}
.newsletter .field{left:321px;top:26px;width:303px;height:37px;background:#fff;border:1px solid #ccc;font-size:13px;color:#666;padding:10px 12px}
.newsletter .signup{left:631px;top:26px;width:110px;height:37px;background:var(--gold);color:#fff;font-size:13px;font-weight:700;display:flex;align-items:center;justify-content:center}
.newsletter .social{left:875px;top:30px;gap:26px}
.newsletter .social span{width:26px;height:26px}
.footer{left:0;top:3617px;width:1200px;height:332px;background:var(--footer)}
.footer h6{font-size:16px;font-weight:900;color:#fff}
.footer ul{list-style:none;margin-top:10px}
.footer li{font-size:14px;color:#e6e6e6;line-height:30.5px}
.contact-row{display:flex;gap:14px;font-size:14px;color:#e6e6e6;line-height:21px}
.contact-row svg{flex:none;margin-top:3px}
.copyright{left:0;top:3949px;width:1200px;height:62px;background:var(--copy);color:#eee;font-size:14px;text-align:center;line-height:62px}
</style>
</head>
<body>

<!-- top bar -->
<div class="abs topbar">
  <div class="abs phone">
    <svg width="14" height="14" viewBox="0 0 24 24"><path fill="#b8862e" d="M6.6 10.8a15 15 0 0 0 6.6 6.6l2.2-2.2c.3-.3.7-.4 1-.2 1.1.4 2.3.6 3.6.6.6 0 1 .4 1 1V20c0 .6-.4 1-1 1A17 17 0 0 1 3 4c0-.6.4-1 1-1h3.5c.6 0 1 .4 1 1 0 1.3.2 2.5.6 3.6.1.3 0 .7-.2 1z"/></svg>
    1-800-555-0148
  </div>
  <div class="abs social" aria-label="Social media links"><span></span><span></span><span></span><span></span><span></span></div>
</div>

<!-- navigation -->
<div class="abs navbar">
  <a class="abs nav-link active" style="left:109px">HOME</a>
  <a class="abs nav-link" style="left:204px">ABOUT US</a>
  <a class="abs nav-link" style="left:329px">OUR SERVICES</a>
  <a class="abs nav-link" style="left:767px">PROJECTS</a>
  <a class="abs nav-link" style="left:890px">BLOG</a>
  <a class="abs nav-link" style="left:979px">CONTACT US</a>
</div>
<svg class="abs brand-plate" width="1200" height="146"><polygon points="490,0 712,0 727,51 475,51" fill="#222"/></svg>
<div class="abs brand nav-brand"><i></i>KVR GLOBALINKS</div>

<!-- hero -->
<div class="abs hero" role="img" aria-label="Red drilling rig on a rocky quarry under a blue cloudy sky"></div>
<h1 class="abs hero-title" style="position:absolute;left:0;top:378px;width:1200px;text-align:center;color:#fff;font-weight:900;font-size:50px;line-height:52px">DRILLING MACHINES<br>ARE MANUFACTURED AND SOLD</h1>
<div class="abs dots"><span></span><span></span><span></span></div>

<!-- welcome -->
<section class="welcome">
  <h2 class="abs">WELCOME TO <em>KVR GLOBALINKS</em></h2>
  <p class="abs" style="top:866px">Lorem ipsum dolor sit amet, consectetur adipiscing elit. Curabitur interdum massa sapien, sed fringilla sem blandit ac. Curabitur at urna ullamcorper, viverra ante eget, vehicula velit. Praesent consectetur dapibus lobortis. Fusce gravida nibh interdum, pulvinar mi in, efficitur leo.</p>
  <p class="abs" style="top:978px">Lorem ipsum dolor sit amet, consectetur adipiscing elit. Curabitur interdum massa sapien, sed fringilla sem blandit ac.</p>
  <div class="abs btn" style="left:75px;top:1059px;width:179px;height:42px">READ MORE</div>
  <div class="abs welcome-frame"></div>
  <div class="abs welcome-img" role="img" aria-label="Businessman in a suit holding a glowing world map in his hand"></div>
</section>

<!-- services -->
<div class="abs services-band"></div>
<div class="abs section-title" style="top:1237px">OUR <em>SERVICES</em></div>
<svg class="abs" style="left:0;top:1178px" width="1200" height="746" viewBox="0 1178 1200 746">
  <circle cx="601" cy="1541" r="207" fill="none" stroke="#999" stroke-width="1.3" stroke-dasharray="6 5"/>
  <circle cx="601" cy="1541" r="152" fill="#151515"/>
  <g fill="#fff" stroke="#e2e2e2">
    <circle cx="470" cy="1386" r="39"/><circle cx="400" cy="1541" r="39"/><circle cx="470" cy="1697" r="39"/>
    <circle cx="805" cy="1541" r="39"/><circle cx="743" cy="1697" r="39"/>
  </g>
  <circle cx="743" cy="1384" r="40" fill="#b8862e" stroke="#fff" stroke-width="4"/>
  <!-- infrastructure -->
  <g fill="#b8862e"><rect x="456" y="1378" width="10" height="22"/><rect x="469" y="1370" width="10" height="30"/><rect x="482" y="1384" width="8" height="16"/></g>
  <!-- oil -->
  <path d="M400 1522c-8 11-12 18-12 24a12 12 0 0 0 24 0c0-6-4-13-12-24z" fill="#b8862e"/>
  <!-- energy -->
  <path d="M474 1676l-14 24h10l-4 18 16-26h-10z" fill="#b8862e"/>
  <!-- agriculture -->
  <path d="M730 1398c0-16 12-26 28-26 0 16-12 26-28 26zm0 0l16-16" fill="#fff" stroke="#fff" stroke-width="2"/>
  <!-- travel -->
  <path d="M805 1526l4 0 3 11 11 5v3l-11-2-2 9 4 3v2l-7-2-7 2v-2l4-3-2-9-11 2v-3l11-5z" fill="#b8862e" transform="rotate(45 805 1541)"/>
  <!-- house -->
  <path d="M743 1681l-16 14h5v14h8v-9h6v9h8v-14h5z" fill="#b8862e"/>
</svg>
<div class="abs brand" style="left:451px;top:1505px;width:300px;font-size:20px"><i></i>KVR GLOBALINKS</div>

<div class="abs svc left" style="left:75px;top:1335px;width:330px"><h3>INFRASTRUCTURE CONSTRUCTION</h3><p>Lorem ipsum dolor sit amet, consectetur adipiscing elit interdum massa sapien se fringilla sem blandit ac.</p></div>
<div class="abs svc left" style="left:90px;top:1500px;width:254px"><h3>OIL</h3><p>Lorem ipsum dolor sit amet, consectetur adipiscing elit interdu mmassa sapien se fringilla</p></div>
<div class="abs svc left" style="left:75px;top:1656px;width:330px"><h3>ENEGY AND GAS SERVICES</h3><p>Lorem ipsum dolor sit amet, consectetur adipiscing elit interdum massa sapien se fringilla sem blandit ac.</p></div>
<div class="abs svc" style="left:797px;top:1335px;width:310px"><h3>AGRICULTURAL PROJECTS</h3><p>Lorem ipsum dolor sit amet, consectetur adipiscing elit interdum massa sapien se fringilla sem blandit ac.</p></div>
<div class="abs svc" style="left:859px;top:1483px;width:270px"><h3>TRAVEL AND TOURISM</h3><p>Lorem ipsum dolor sit amet, consectetur adipiscing elit interdum massa sapien se fringilla sem blandit ac.</p></div>
<div class="abs svc" style="left:797px;top:1656px;width:310px"><h3>REAL ESTATE DEVELOPMENT</h3><p>Lorem ipsum dolor sit amet, consectetur adipiscing elit interdum massa sapien se fringilla sem blandit ac.</p></div>
<div class="abs btn" style="left:487px;top:1817px;width:226px;height:42px">VIEW ALL SERVICES</div>

<!-- projects -->
<div class="abs section-title" style="top:1992px">OUR <em>PROJECTS</em></div>
<div class="abs" role="img" aria-label="Yellow drilling machine in a snowy forest" style="left:75px;top:2060px;width:330px;height:212px;background:linear-gradient(160deg,#aebfcc,#5f7684 60%,#c9a23a)"></div>
<div class="abs" role="img" aria-label="Aerial view of a large building complex under construction" style="left:436px;top:2060px;width:330px;height:212px;background:linear-gradient(160deg,#9aa19a,#c7c7c2 50%,#7f8578)"></div>
<div class="abs" role="img" aria-label="Offshore oil platform at sea" style="left:797px;top:2060px;width:330px;height:212px;background:linear-gradient(180deg,#b7b0a3,#3e5b63 40%,#1f3a44)"></div>
<div class="abs project" style="left:75px;top:2296px;width:330px"><h3>PROJECT HEADING</h3><p>Lorem ipsum dolor sit amet, consectetur<br>adipiscing elit interdum.</p></div>
<div class="abs project" style="left:436px;top:2296px;width:330px"><h3>PROJECT HEADING</h3><p>Lorem ipsum dolor sit amet, consectetur<br>adipiscing elit interdum.</p></div>
<div class="abs project" style="left:797px;top:2296px;width:330px"><h3>PROJECT HEADING</h3><p>Lorem ipsum dolor sit amet, consectetur<br>adipiscing elit interdum.</p></div>
<div class="abs btn" style="left:151px;top:2404px;width:179px;height:43px">READ MORE</div>
<div class="abs btn" style="left:512px;top:2404px;width:179px;height:43px">READ MORE</div>
<div class="abs btn" style="left:873px;top:2404px;width:179px;height:43px">READ MORE</div>

<!-- blog -->
<div class="abs blog-band"></div>
<div class="abs section-title" style="top:2576px">BLOG <em>POSTS</em></div>
<div class="abs" role="img" aria-label="Construction workers on a building site at sunset" style="left:75px;top:2647px;width:179px;height:129px;background:linear-gradient(160deg,#d9b887,#a0704a 60%,#5a4a3c)"></div>
<div class="abs" role="img" aria-label="Worker beside grain silos" style="left:615px;top:2647px;width:179px;height:129px;background:linear-gradient(160deg,#6f7d8c,#b2b6b8 50%,#404852)"></div>
<div class="abs" role="img" aria-label="Offshore oil rig under a blue sky" style="left:75px;top:2823px;width:179px;height:129px;background:linear-gradient(180deg,#4f83bc,#8fb3d6 55%,#2d5d86)"></div>
<div class="abs" role="img" aria-label="Drilling rig in a quarry" style="left:615px;top:2823px;width:179px;height:129px;background:linear-gradient(180deg,#4d86c7,#a9c3db 45%,#7d6a55)"></div>
<div class="abs post" style="left:271px;top:2645px"><div class="date">JANUARY 18, 2019</div><h4>MAURIS ARCU TRISTIQUE URNA</h4><p>Lorem ipsum dolor sit amet, consectetur adipiscing elit interdum a imperdiet ultrices, velit magna faucibus.</p></div>
<div class="abs post" style="left:811px;top:2645px"><div class="date">JANUARY 18, 2019</div><h4>MAURIS ARCU TRISTIQUE URNA</h4><p>Lorem ipsum dolor sit amet, consectetur adipiscing elit interdum a imperdiet ultrices, velit magna faucibus.</p></div>
<div class="abs post" style="left:271px;top:2822px"><div class="date">JANUARY 18, 2019</div><h4>MAURIS ARCU TRISTIQUE URNA</h4><p>Lorem ipsum dolor sit amet, consectetur adipiscing elit interdum a imperdiet ultrices, velit magna faucibus.</p></div>
<div class="abs post" style="left:811px;top:2822px"><div class="date">JANUARY 18, 2019</div><h4>MAURIS ARCU TRISTIQUE URNA</h4><p>Lorem ipsum dolor sit amet, consectetur adipiscing elit interdum a imperdiet ultrices, velit magna faucibus.</p></div>

<!-- reviews -->
<div class="abs section-title" style="top:3071px">CUSTOMER <em>REVIEWS</em></div>
<div class="abs" style="left:0;top:3120px;width:1200px;text-align:center;font-size:100px;font-weight:900;color:var(--green);line-height:100px;font-family:Georgia,serif">&rdquo;</div>
<p class="abs quote-text">After days at sea, I really enjoy sitting in some coffeeshop, opening my computer and connecting with other Penwise writers and work with words instead of ropes and sails. And more! With Penwise, I have discovered some corners of the digital world that I would otherwise have never visited. So, even while working I keep traveling.</p>
<svg class="abs" style="left:74px;top:3264px" width="24" height="36"><path d="M20 3L6 18l14 15" fill="none" stroke="#444" stroke-width="4"/></svg>
<svg class="abs" style="left:1103px;top:3264px" width="24" height="36"><path d="M4 3l14 15L4 33" fill="none" stroke="#444" stroke-width="4"/></svg>
<div class="abs reviewer" style="left:364px;top:3313px"><div class="face" role="img" aria-label="Customer portrait"></div><b>NAME HEADING</b><small>Location</small></div>
<div class="abs reviewer" style="left:518px;top:3313px"><div class="face mid" role="img" aria-label="Customer portrait"></div><b>NAME HEADING</b><small>Location</small></div>
<div class="abs reviewer" style="left:674px;top:3313px"><div class="face" role="img" aria-label="Customer portrait"></div><b>NAME HEADING</b><small>Location</small></div>

<!-- newsletter -->
<div class="abs newsletter">
  <h5 class="abs">NEWSLETTER SIGN UP</h5>
  <div class="abs field">Enter Email Address</div>
  <div class="abs signup">SIGN UP</div>
  <div class="abs social" aria-label="Social media links"><span></span><span></span><span></span><span></span><span></span></div>
</div>

<!-- footer -->
<div class="abs footer">
  <div class="abs" style="left:79px;top:62px"><h6>SITE MAP</h6><ul><li>Home</li><li>About Us</li><li>Services</li><li>Projects</li><li>Blog</li><li>Contact Us</li></ul></div>
  <div class="abs" style="left:282px;top:62px"><h6>SERVICES</h6><ul><li>Praesent consectetur</li><li>Dapibus lobortis</li><li>Fusce gravida nibh</li><li>Interdum</li><li>Pulvinar miin</li><li>Efficitur leo</li></ul></div>
  <div class="abs brand" style="left:451px;top:70px;width:300px"><i></i>KVR GLOBALINKS</div>
  <div class="abs" style="left:811px;top:62px">
    <h6>CONTACT INFO</h6>
    <div class="contact-row" style="margin-top:12px"><svg width="12" height="14" viewBox="0 0 24 28"><path fill="#fff" d="M12 0a10 10 0 0 0-10 10c0 8 10 18 10 18s10-10 10-18A10 10 0 0 0 12 0zm0 14a4 4 0 1 1 0-8 4 4 0 0 1 0 8z"/></svg><span>14 Harbor Point, Street Name<br>New York City, USA</span></div>
    <div class="contact-row" style="margin-top:14px"><svg width="13" height="13" viewBox="0 0 24 24"><path fill="#fff" d="M6.6 10.8a15 15 0 0 0 6.6 6.6l2.2-2.2c.3-.3.7-.4 1-.2 1.1.4 2.3.6 3.6.6.6 0 1 .4 1 1V20c0 .6-.4 1-1 1A17 17 0 0 1 3 4c0-.6.4-1 1-1h3.5c.6 0 1 .4 1 1 0 1.3.2 2.5.6 3.6.1.3 0 .7-.2 1z"/></svg><span>1-800-555-0148</span></div>
    <div class="contact-row" style="margin-top:14px"><svg width="13" height="11" viewBox="0 0 24 18"><path fill="#fff" d="M0 0h24v18H0zm2 2v1l10 7 10-7V2z"/></svg><span>hello@kvrglobalinks.com</span></div>
    <div class="contact-row" style="margin-top:14px;padding-left:27px"><span>Map Location</span></div>
  </div>
</div>
<div class="abs copyright">Copyright © 2020 KVR Globalinks. All Right Reserved</div>

</body>
</html>
```